Website Refresh

I'm looking to refresh my Squarespace website. www.derekmulvane.com

I am pretty happy with the content but would like a better navigation bar, livelier color choices, consistent type faces, and a more modern look. I am willing to pay extra to implement suggested improvements that would make the site more appealing

```html
<!DOCTYPE html>
<html lang="en">
<head>
<meta charset="utf-8">
<title>Peerwise – Derek Mulvane</title>
<link href="https://fonts.googleapis.com/css2?family=Poppins:wght@400;500;600;700&family=Roboto:wght@400;500&family=Rubik:wght@500&display=swap" rel="stylesheet">
<style>
:root{
  --navy:#12395e;
  --purple:#3a1263;
  --gold:#e6cc7c;
  --ink:#222;
  --grey:#555;
  --light:#eeeef0;
  --black:#000;
}
*{box-sizing:border-box;margin:0;padding:0}
html,body{width:1200px;height:3950px;overflow:hidden;background:#fff;font-family:"Poppins",sans-serif;color:var(--ink)}
.abs{position:absolute}
section,header,nav,footer{position:relative;width:1200px}
/* header */
.topbar{height:103px}
.brand{left:110px;top:34px;display:flex;align-items:center;gap:10px}
.brand-mark{width:22px;height:22px;border-radius:50%;background:var(--purple)}
.brand-name{font:500 26px/1 "Poppins",sans-serif;color:var(--purple)}
.social{top:38px;left:627px;display:flex;gap:9px}
.dot{width:26px;height:26px;border-radius:50%}
.lang{left:756px;top:42px;font:600 13px "Poppins",sans-serif}
.flag{left:802px;top:38px;width:26px;height:26px;border-radius:50%;background:linear-gradient(#c8102e 0 50%,#fff 50% 60%,#c8102e 60%)}
.call{left:862px;top:24px}
.call-label{left:922px;top:28px;font:500 14px "Poppins",sans-serif}
.call-num{left:922px;top:48px;font:600 21px "Poppins",sans-serif;color:var(--navy)}
.nav{height:57px;background:var(--purple);display:flex;padding-left:131px}
.nav a{color:#fff;text-decoration:none;font:600 13px/57px "Poppins",sans-serif;padding:0 12px}
.nav a.active{background:var(--gold);color:var(--purple)}
/* hero */
.hero{height:628px;background:linear-gradient(135deg,#5b5049,#3c3732 45%,#2a2622)}
.hero h1{position:absolute;top:262px;width:100%;text-align:center;color:#fff;font:700 40px "Poppins",sans-serif}
.hero p{position:absolute;top:326px;width:100%;text-align:center;color:#fff;font:500 15px/26px "Poppins",sans-serif}
.btn{display:flex;align-items:center;justify-content:center;background:var(--gold);color:var(--purple);border-radius:24px;font:600 13px "Poppins",sans-serif}
.hero .btn{position:absolute;left:532px;top:400px;width:136px;height:40px}
.arrow{width:40px;height:40px;border-radius:50%;background:rgba(255,255,255,.25);top:263px;color:#fff;text-align:center;line-height:40px;font-size:18px}
/* membership */
.member{height:1127px}
.h2{font:600 35px/43px "Poppins",sans-serif;color:var(--navy);text-align:center}
.member .h2{position:absolute;top:108px;width:100%}
.trait{top:235px;width:196px;text-align:center}
.ring{width:194px;height:194px;border-radius:50%;border:3px solid #888;display:flex;align-items:center;justify-content:center}
.ring.on{border-color:var(--purple)}
.ring-in{width:172px;height:172px;border-radius:50%;border:4px solid var(--gold);display:flex;align-items:center;justify-content:center}
.trait h3{margin-top:24px;font:500 20px/26px "Rubik",sans-serif;color:#222}
.pitch{top:585px;width:100%;text-align:center;color:var(--navy);font:500 21px/26px "Poppins",sans-serif}
.photo{left:112px;top:752px;width:462px;height:280px;background:linear-gradient(120deg,#b9aea2,#8d8478 50%,#5d564f);border-radius:3px}
.about-text{left:600px;top:749px;width:490px;font:400 13.5px/21.5px "Poppins",sans-serif;color:var(--grey)}
.about-text p+p{margin-top:21px}
.member .btn{position:absolute;left:600px;top:992px;width:136px;height:40px}
/* video */
.video{height:797px;background:var(--light)}
.video .h2{position:absolute;top:90px;width:100%}
.video .sub{position:absolute;top:145px;width:100%;text-align:center;font:400 17px/28px "Roboto",sans-serif;color:#444}
.clip{background:linear-gradient(135deg,#3f4d3a,#6a6560 55%,#9a8f88);border-radius:3px;display:flex;align-items:center;justify-content:center}
.play{width:22px;height:22px;border-radius:50%;background:rgba(0,0,0,.45)}
.play.big{width:52px;height:36px;border-radius:9px;background:#c8232c}
/* blog */
.blog{height:738px}
.blog-band{left:0;top:0;width:1200px;height:218px;background:var(--purple)}
.blog-kicker{top:40px;width:100%;text-align:center;color:#fff;font:400 23px "Poppins",sans-serif}
.blog-title{top:74px;width:100%;text-align:center;color:#fff;font:700 38px "Poppins",sans-serif}
.card{top:156px;width:314px;height:400px;background:#fff;box-shadow:0 4px 14px rgba(0,0,0,.12);text-align:center}
.card-img{height:272px;border-bottom:5px solid var(--purple)}
.date{position:absolute;top:263px;left:50%;transform:translateX(-50%);background:var(--gold);color:#222;font:600 11.5px/20px "Poppins",sans-serif;padding:0 16px;border-radius:3px 3px 0 0}
.card h4{margin-top:25px;font:600 14.5px/24px "Poppins",sans-serif;color:#222;padding:0 10px}
.card a{display:inline-block;margin-top:4px;font:500 12px "Poppins",sans-serif;color:#222;text-decoration:underline}
.blog .btn{position:absolute;left:498px;top:588px;width:205px;height:35px}
/* footer */
.footer{height:502px;background:var(--black);color:#fff}
.f-h{top:117px;font:500 18px "Roboto",sans-serif}
.field{background:#fff;color:#666;font:400 13px "Roboto",sans-serif;padding:0 18px;line-height:38px;height:38px}
.submit{left:112px;top:346px;width:134px;height:46px;border-radius:24px;background:var(--gold);color:var(--purple);font:600 15px "Roboto",sans-serif;display:flex;align-items:center;justify-content:center}
.links{left:650px;top:150px;list-style:none;font:400 15px/30px "Roboto",sans-serif}
.links li::before{content:"»";margin-right:12px}
.contact{left:848px;font:400 15px/23px "Roboto",sans-serif;display:flex;gap:12px}
.contact svg{flex:none;margin-top:4px}
.connect{left:650px;top:367px;font:500 18px "Roboto",sans-serif}
.rule{left:112px;top:443px;width:976px;height:1px;background:#444}
.copy{top:457px;width:100%;text-align:center;font:400 14px "Roboto",sans-serif}
</style>
</head>
<body>
<header class="topbar">
  <div class="abs brand"><span class="brand-mark"></span><span class="brand-name">Peerwise</span></div>
  <div class="abs social"><span class="dot" style="background:#3b5998"></span><span class="dot" style="background:#1da1f2"></span><span class="dot" style="background:#dd4b39"></span></div>
  <div class="abs lang">Eng ⌄</div>
  <div class="abs flag"></div>
  <svg class="abs call" width="48" height="52" viewBox="0 0 48 52"><circle cx="24" cy="26" r="21" fill="none" stroke="var(--purple)" stroke-width="3"/><path d="M16 17c2-2 4-2 5 0l2 4c1 2 0 3-1 4 1 3 3 5 6 6 1-1 2-2 4-1l4 2c2 1 2 3 0 5-3 3-8 2-14-4s-9-12-6-16z" fill="var(--purple)"/></svg>
  <div class="abs call-label">Call us Today :</div>
  <div class="abs call-num">+1 888 888 8888</div>
</header>
<nav class="nav">
  <a class="active">ABOUT</a><a>MEMBER VIDEO TESTIMONIALS</a><a>TESTIMONIALS</a><a>SUCCESS STORIES</a><a>DEREK’S BLOG</a><a>DEREK MULVANE BIO</a><a>JOIN THE GROUP</a>
</nav>
<section class="hero" role="img" aria-label="Executives meeting around a boardroom table">
  <div class="abs arrow" style="left:70px">‹</div>
  <div class="abs arrow" style="left:1088px">›</div>
  <h1>TURNING GOOD CEOS INTO GREAT CEOS</h1>
  <p>Our award winning CEOs will help you make better decisions for your company,<br>family, and community .</p>
  <span class="btn">GET STARTED</span>
</section>
<section class="member">
  <h2 class="h2">MEMBERSHIP IS BY INVITATION<br>ONLY FOR THOSE WHO</h2>
  <div class="abs trait" style="left:114px"><div class="ring"><div class="ring-in"><svg width="58" height="58" viewBox="0 0 24 24"><path d="M2 10h4v11H2zM8 10l4-8c2 0 3 1 3 3l-1 4h6c1 0 2 1 2 2l-2 8c0 1-1 2-2 2H8z" fill="var(--purple)"/></svg></div></div><h3>Open to being<br>challenged</h3></div>
  <div class="abs trait" style="left:373px"><div class="ring"><div class="ring-in"><svg width="58" height="50" viewBox="0 0 24 20"><path d="M2 1v17h21" fill="none" stroke="var(--purple)" stroke-width="2.5"/><path d="M5 14l5-6 4 4 7-7" fill="none" stroke="var(--purple)" stroke-width="2.5"/><path d="M16 4h6v6z" fill="var(--purple)"/></svg></div></div><h3>Commit to double<br>digit growth</h3></div>
  <div class="abs trait" style="left:633px"><div class="ring on"><div class="ring-in"><svg width="62" height="56" viewBox="0 0 24 22"><rect x="1" y="1" width="22" height="14" rx="2" fill="none" stroke="var(--purple)" stroke-width="2.5"/><path d="M10 15v4M14 15v4M6 20h12" stroke="var(--purple)" stroke-width="2.5"/></svg></div></div><h3>Ongoing<br>learning</h3></div>
  <div class="abs trait" style="left:893px"><div class="ring"><div class="ring-in"><svg width="58" height="58" viewBox="0 0 24 24"><path d="M12 1l3.3 7 7.7.8-5.8 5.2 1.7 7.6L12 17.8 5.1 21.6l1.7-7.6L1 8.8 8.7 8z" fill="var(--purple)"/></svg></div></div><h3>Giving &amp; receiving<br>honest feedback</h3></div>
  <div class="abs pitch">If you are lonely with no one you can trust to talk through tough decisions<br>If you don’t have the right people in the right seats<br><span style="display:block;height:24px"></span>If you seek financial independence, professional and personal growth, and<br>avoiding burnout; our group might be right for you.</div>
  <div class="abs photo" role="img" aria-label="Leader presenting to a small group in an office"></div>
  <div class="abs about-text">
    <p>After many years in the business world as the founder/CEO of six for-profit and five not-for-profit corporations, I understand the huge responsibility you have for making the right decisions for your company, the personal well-being of your employees and yourself.</p>
    <p>Our Peerwise group is made up of 15 other smart CEOs who have been where you are. We meet monthly in a safe, confidential environment to discuss critical business decisions, opportunities, and challenges. Additionally I meet with each member two hours/monthly for a private coaching session.</p>
  </div>
  <span class="btn">LEARN MORE</span>
</section>
<section class="video">
  <h2 class="h2">OUR VIDEO</h2>
  <p class="sub">Our award winning CEOs will help you make better decisions for your<br>company, family, and community</p>
  <div class="abs clip" style="left:112px;top:247px;width:440px;height:450px" role="img" aria-label="Member testimonial video"><span class="play big"></span></div>
  <div class="abs clip" style="left:562px;top:247px;width:260px;height:220px" role="img" aria-label="Member testimonial video"><span class="play"></span></div>
  <div class="abs clip" style="left:830px;top:247px;width:260px;height:220px" role="img" aria-label="Member testimonial video"><span class="play"></span></div>
  <div class="abs clip" style="left:562px;top:477px;width:260px;height:220px" role="img" aria-label="Member testimonial video"><span class="play"></span></div>
  <div class="abs clip" style="left:830px;top:477px;width:260px;height:220px" role="img" aria-label="Member testimonial video"><span class="play"></span></div>
</section>
<section class="blog">
  <div class="abs blog-band"></div>
  <div class="abs blog-kicker">DEREK’S BLOG</div>
  <div class="abs blog-title">LATEDT NEWS AND UPDATES</div>
  <article class="abs card" style="left:112px"><div class="card-img" role="img" aria-label="Team discussion around a table" style="background:linear-gradient(135deg,#8c8378,#4d463f)"></div><span class="date">Jan 07, 2022</span><h4>WHAT ARE OKRS AND HOW<br>YOUR TEAM SHOULD ADOPT THEM</h4><a>Learn More &gt;</a></article>
  <article class="abs card" style="left:443px"><div class="card-img" role="img" aria-label="Group portrait of peer CEOs" style="background:linear-gradient(160deg,#4f8a6a,#5b6a8a 50%,#2e3550)"></div><span class="date">Jan 07, 2022</span><h4>IMPRESSIVE PEER CEOS<br>JOIN A DIVERSE BLEND OF 17</h4><a>Learn More &gt;</a></article>
  <article class="abs card" style="left:775px"><div class="card-img" role="img" aria-label="Growth graphic showing plus 4.6 percent for member companies" style="background:linear-gradient(#f4d64a,#f39a1d 60%,#e7411c)"></div><span class="date">Jan 07, 2022</span><h4>PROVEN PEERWISE METHODOLOGY<br>ACCORDING TO CRANE &amp; HOLLOWAY,</h4><a>Learn More &gt;</a></article>
  <span class="btn">READ MORE NEWS</span>
</section>
<footer class="footer">
  <div class="abs f-h" style="left:112px">GET IN TOUCH</div>
  <div class="abs field" style="left:112px;top:154px;width:234px">First Name</div>
  <div class="abs field" style="left:354px;top:154px;width:234px">Last Name</div>
  <div class="abs field" style="left:112px;top:202px;width:234px">Email</div>
  <div class="abs field" style="left:354px;top:202px;width:234px">phone number</div>
  <div class="abs field" style="left:112px;top:252px;width:476px;height:72px;line-height:32px">Message</div>
  <div class="abs submit">SUBMIT</div>
  <div class="abs f-h" style="left:650px">QUICK LINKS</div>
  <ul class="abs links"><li>Home</li><li>About Us</li><li>Meet Our Staff</li><li>Our Services</li><li>Testimonials</li><li>Contact Us</li></ul>
  <div class="abs f-h" style="left:848px">CONTACT US</div>
  <div class="abs contact" style="top:150px"><svg width="12" height="16" viewBox="0 0 12 16"><path d="M6 0a6 6 0 0 0-6 6c0 4 6 10 6 10s6-6 6-10a6 6 0 0 0-6-6zm0 8.5A2.5 2.5 0 1 1 6 3.5a2.5 2.5 0 0 1 0 5z" fill="#fff"/></svg><span>Lorem ipsum dolor sit amet,<br>consectetur adipi</span></div>
  <div class="abs contact" style="top:230px"><svg width="12" height="16" viewBox="0 0 12 16"><rect x="2" y="1" width="8" height="14" rx="1.5" fill="none" stroke="#fff" stroke-width="1.6"/></svg><span>+1 888 888 8888</span></div>
  <div class="abs contact" style="top:264px"><svg width="16" height="12" viewBox="0 0 16 12"><rect x="1" y="1" width="14" height="10" rx="1" fill="none" stroke="#fff" stroke-width="1.5"/><path d="M1 1l7 6 7-6" fill="none" stroke="#fff" stroke-width="1.5"/></svg><span>info@companyname.com</span></div>
  <div class="abs connect">STAY CONNECTED :</div>
  <span class="abs dot" style="left:850px;top:364px;background:#3b5998"></span>
  <span class="abs dot" style="left:889px;top:364px;background:#c13584"></span>
  <div class="abs rule"></div>
  <div class="abs copy">© 2022 Company Name &nbsp;| All Rights Reserved | Terms and Conditions</div>
</footer>
</body>
</html>
```